Wellness, Meaning, and the Inner Journey Research Program Website

Overview: This website will serve a new research program (Wellness, Meaning, and the Inner Journey) at the Harrowgate University School of Medicine. I want a clean, intuitive design that has a navigation bar, but uses icons/graphic buttons to link to the main pages. In an attached Word document, I have provided a basic information architecture for the site, understanding that this project would just generate graphics and code for the 3 pages. I highlighted the 3 pages I'd like designed.
Target market: People who want to participate in our research, or contribute grant funding to specific projects.
Number of page: The design project focuses on 3 pages, but the site must accommodate 6 pages with top-level links. See attached Word doc.
Logo and website header: Please integrate our logo in the header. I've uploaded it as a png file--both with the name of the website and with just the logo image. I imaging the logo would look great in a banner set against an image of a mountain. The two main design themes I want to see included are nature and healthcare.
Text content: I have not yet provided text. Use some dummy text.
Technical Specifications:
- Build using WordPress. We will host this site ourselves on NetHarbor using WordPress.
- The design package must be coded.
- The template must be responsive to different platforms (e.g., computer, mobile phone, iPad).
Thank you! I look forward to seeing your designs.
- Ned

```html
<!DOCTYPE html>
<html lang="en">
<head>
<meta charset="utf-8">
<title>Wellness, Meaning, and the Inner Journey – The Research Program</title>
<link href="https://fonts.googleapis.com/css2?family=Lato:ital,wght@0,400;0,700;0,900;1,400;1,700;1,900&display=swap" rel="stylesheet">
<style>
:root{
  --navy:#124a85;
  --green:#6ba224;
  --forest:#1a6249;
  --band:#245f8a;
  --band-light:#4374a3;
  --sage:#66a38f;
  --ink:#2b2b2b;
  --grey:#e8e8e9;
  --dark:#1b1b1b;
  --white:#fff;
}
*{box-sizing:border-box;margin:0;padding:0}
html,body{width:1200px;height:3913px;overflow:hidden}
body{position:relative;background:var(--white);font-family:'Lato',sans-serif;color:var(--ink)}
.abs{position:absolute}
svg{display:block}

/* header */
.site-header{top:0;left:0;width:1200px;height:109px;background:var(--white);z-index:3}
.brand{display:flex;align-items:center;gap:10px;left:76px;top:32px}
.brand-dot{width:40px;height:40px;border-radius:50%;background:var(--green)}
.brand-name{font-weight:700;font-size:14px;line-height:17px;color:var(--navy)}
.brand-name span{display:block;color:var(--navy);font-weight:700;font-size:11px}
.nav a{position:absolute;top:48px;transform:translateX(-50%);font-size:15px;font-weight:700;color:var(--ink);text-decoration:none;white-space:nowrap}
.nav a.active{color:var(--navy)}

/* hero */
.hero{top:109px;left:0;width:1200px;height:700px;background:linear-gradient(100deg,#eceef0 0%,#dcdcdc 35%,#b9aca1 62%,#8d7867 80%,#d7d5d3 100%)}
.hero-title{left:76px;top:322px;font-weight:900;font-size:48px;line-height:57px;color:var(--navy)}
.hero-sub{left:76px;top:434px;font-weight:900;font-style:italic;font-size:32px;color:var(--green)}
.btn{display:flex;align-items:center;justify-content:center;background:var(--forest);color:var(--white);border-radius:30px;font-weight:700;text-decoration:none}
.hero-btn{left:76px;top:501px;width:194px;height:43px;font-size:17px}
.dots{display:flex;gap:9px}
.dots i{display:block;width:12px;height:12px;border-radius:50%;background:var(--white)}
.dots i.on{background:var(--forest)}
.hero-dots{left:564px;top:668px}
.hero-wave{left:0;top:720px}

/* pillars */
.pillar{width:330px;height:330px;border-radius:50%;top:908px;color:var(--white);text-align:center;padding-top:40px}
.pillar svg{margin:0 auto 10px}
.pillar h3{font-size:24px;font-weight:900;margin-bottom:12px}
.pillar p{font-size:14px;line-height:23px;padding:0 34px}
.p-health{left:75px;background:var(--navy)}
.p-values{left:438px;background:var(--green)}
.p-spirit{left:797px;background:var(--forest)}

/* vision */
.vision-bg{left:0;top:1355px}
.vision-photo{left:122px;top:1463px;width:434px;height:434px;border-radius:50%;background:radial-gradient(circle at 62% 45%,#f6c670 0%,#d88a3b 18%,#7d5b3a 45%,#4c4a35 75%,#3b3f2c 100%)}
.vision-title{left:640px;width:470px;top:1568px;text-align:center;font-weight:900;font-size:46px;color:var(--white)}
.vision-quote{left:640px;width:470px;top:1630px;text-align:center;font-style:italic;font-size:18px;line-height:30.5px;color:var(--white)}

/* people */
.people-title{left:75px;top:2105px;font-size:45px;font-weight:900;color:var(--ink)}
.people-text{left:75px;top:2180px;width:570px;font-size:16.5px;line-height:27.7px;color:var(--ink)}
.people-text p+p{margin-top:6px}
.people-btn{left:75px;top:2436px;width:216px;height:60px;font-size:20px}
.people-photo{left:690px;top:2090px;width:434px;height:434px;border-radius:50%;background:linear-gradient(135deg,#3b3a4d 0%,#2e5f8a 35%,#2aa3a7 60%,#c9b9a6 80%,#6b4a36 100%)}

/* projects */
.projects-bg{left:0;top:2576px}
.section-title{left:0;width:1200px;text-align:center;font-size:37px;font-weight:900;color:var(--ink)}
.projects-title{top:2645px}
.card{top:2722px;width:450px;height:234px;background:var(--white);border-radius:6px}
.card-1{left:137px}.card-2{left:676px}
.card-img{top:2746px;width:193px;height:185px;border-radius:6px}
.img-1{left:74px;background:linear-gradient(160deg,#6f5aa6 0%,#c96a9c 40%,#f0a46a 70%,#3a2a2a 100%)}
.img-2{left:614px;background:linear-gradient(150deg,#dad7d2 0%,#b9c3c8 45%,#5b6670 75%,#e6e2dc 100%)}
.card-body{top:2770px;width:270px}
.cb-1{left:298px}.cb-2{left:832px}
.card-body h4{font-size:18px;font-weight:900;color:var(--forest);margin-bottom:10px}
.card-body p{font-size:14px;line-height:23px;color:var(--ink)}
.card-body a{display:block;margin-top:14px;font-size:14px;font-weight:900;color:var(--navy);text-decoration:none}
.proj-dots{left:573px;top:2992px}
.proj-dots i{background:#777}
.proj-dots i.on{background:var(--forest)}

/* faq */
.faq-title{top:3145px}
.faq-item{left:173px;width:850px;font-size:21px;color:var(--ink);display:flex;justify-content:space-between;align-items:center}
.faq-item b{font-size:26px;font-weight:900}

/* footer */
.footer-bg{left:0;top:3515px}
.footer-brand{left:76px;top:3694px}
.f-col h5{font-size:15px;font-weight:900;color:var(--ink);margin-bottom:12px}
.f-col a{display:block;font-size:13px;color:var(--ink);text-decoration:none}
.col-map{left:433px;top:3620px}.col-map a{line-height:30.4px}
.col-res{left:623px;top:3620px}.col-res a{line-height:33.7px}
.col-mail{left:832px;top:3620px}
.subscribe{left:832px;top:3661px;width:269px;height:41px;background:var(--white);border-radius:21px;overflow:hidden}
.subscribe span{position:absolute;left:20px;top:12px;font-size:13px;color:#555}
.subscribe b{position:absolute;right:0;top:0;width:48px;height:41px;background:var(--forest);color:var(--white);font-size:15px;display:flex;align-items:center;justify-content:center}
.social{left:832px;top:3738px;display:flex;gap:24px}
.social i{display:block;width:18px;height:18px;border-radius:50%;background:var(--ink)}
.copyright{left:0;top:3854px;width:1200px;height:59px;background:var(--dark);color:#bbb;font-size:12px;display:flex;align-items:center;justify-content:center}
</style>
</head>
<body>

<header class="site-header abs">
  <div class="brand abs">
    <div class="brand-dot"></div>
    <div class="brand-name">Wellness, Meaning, and the Inner Journey<span>The Research Program</span></div>
  </div>
  <nav class="nav">
    <a class="active" style="left:515px" href="#">HOME</a>
    <a style="left:609px" href="#">PEOPLE</a>
    <a style="left:717px" href="#">PROJECTS</a>
    <a style="left:823px" href="#">FAQS</a>
    <a style="left:937px" href="#">RESOURCES</a>
    <a style="left:1077px" href="#">CONTACT US</a>
  </nav>
</header>

<section class="hero abs" role="img" aria-label="Photo of a woman smelling wild lavender in a sunlit field"></section>
<h1 class="hero-title abs">WELLNESS, MEANING &amp;<br>THE INNER JOURNEY</h1>
<div class="hero-sub abs">The-Research-Program</div>
<a class="btn hero-btn abs" href="#">READ MORE</a>
<div class="dots hero-dots abs"><i class="on"></i><i></i><i></i><i></i></div>
<svg class="hero-wave abs" width="1200" height="100" viewBox="0 0 1200 100"><path d="M0 40 C200 110 420 110 640 60 C840 15 1020 10 1200 80 L1200 100 L0 100Z" fill="#fff"/></svg>

<section class="pillars">
  <div class="pillar p-health abs">
    <svg width="70" height="70" viewBox="0 0 70 70" fill="none" stroke="#fff" stroke-width="2.5"><path d="M35 50 C15 36 10 26 16 18 C22 10 32 14 35 20 C38 14 48 10 54 18"/><circle cx="58" cy="14" r="8"/><path d="M58 10v8M54 14h8"/><path d="M8 48h10l14 6h14l12-8M14 44v18h-6"/></svg>
    <h3>HEALTHCARE</h3>
    <p>Praesent quis dapibus orci, a interdum ligula. Sed rutrum dignissim hendrerit laoreet molestie diam...</p>
  </div>
  <div class="pillar p-values abs">
    <svg width="70" height="70" viewBox="0 0 70 70" fill="none" stroke="#fff" stroke-width="2.5"><circle cx="22" cy="14" r="6"/><circle cx="35" cy="11" r="6"/><circle cx="48" cy="14" r="6"/><path d="M14 34c0-8 16-8 16 0M27 31c0-8 16-8 16 0M40 34c0-8 16-8 16 0"/><path d="M8 46h10l14 6h14l14-10M14 42v18h-6"/></svg>
    <h3>VALUES</h3>
    <p>Praesent quis dapibus orci, a interdum ligula. Sed rutrum dignissim hendrerit laoreet molestie diam...</p>
  </div>
  <div class="pillar p-spirit abs">
    <svg width="70" height="70" viewBox="0 0 70 70" fill="none" stroke="#fff" stroke-width="2.5"><circle cx="35" cy="36" r="14"/><path d="M35 6 L58 58 L12 58 Z"/></svg>
    <h3>SPIRITUAL LIFE</h3>
    <p>Praesent quis dapibus orci, a interdum ligula. Sed rutrum dignissim hendrerit laoreet molestie diam...</p>
  </div>
</section>

<svg class="vision-bg abs" width="1200" height="650" viewBox="0 0 1200 650">
  <path d="M0 10 C250 -30 420 40 600 50 C800 60 1000 -10 1200 10 L1200 640 L0 640Z" fill="var(--sage)"/>
  <path d="M0 15 C200 40 380 85 600 70 C820 55 1000 25 1200 20 L1200 630 C1000 560 800 560 600 590 C400 620 200 560 0 610Z" fill="var(--band-light)"/>
  <path d="M0 70 C200 45 400 5 600 30 C800 55 1000 80 1200 60 L1200 580 C1000 545 800 540 600 565 C400 590 200 600 0 570Z" fill="var(--band)"/>
  <path d="M0 640 C250 560 420 555 600 570 C800 590 1000 620 1200 560 L1200 650 L0 650Z" fill="#fff"/>
  <path d="M0 600 C250 530 420 520 600 545 C800 570 1000 620 1200 650 L0 650Z" fill="var(--sage)" opacity=".85"/>
</svg>
<div class="vision-photo abs" role="img" aria-label="Photo of a person meditating on a mountain top at sunset"></div>
<h2 class="vision-title abs">VISION STATEMENT</h2>
<p class="vision-quote abs">“ Sed ut perspiciatis unde omnis iste natus error sit voluptatem accusantium doloremque laudantium, totam rem aperiam, eaque ipsa quae ab illo inventore veritatis et quasi architecto beatae vitae dicta sunt explicabo...”</p>

<h2 class="people-title abs">PEOPLE</h2>
<div class="people-text abs">
  <p>Sed ut perspiciatis unde omnis iste natus error sit voluptatem accusantium doloremque laudantium, totam rem aperiam, eaque ipsa quae ab illo inventore veritatis et quasi architecto beatae vitae dicta sunt explicabo. Nemo enim ipsam voluptatem quia voluptas sit aspernatur aut odit aut fugit, sed quia consequuntur magni dolores eos qui ratione voluptatem sequi nesciunt.</p>
  <p>Neque porro quisquam est, qui dolorem ipsum quia dolor sit amet, consectetur, adipisci velit, sed quia non numquam.</p>
</div>
<a class="btn people-btn abs" href="#">READ MORE</a>
<div class="people-photo abs" role="img" aria-label="Photo of a care worker helping an older woman fill in a form"></div>

<svg class="projects-bg abs" width="1200" height="510" viewBox="0 0 1200 510"><path d="M0 60 C300 -5 900 -5 1200 60 L1200 440 C900 500 300 520 0 430Z" fill="var(--grey)"/></svg>
<h2 class="section-title projects-title abs">RESEARCH PROJECTS</h2>
<div class="card card-1 abs"></div>
<div class="card card-2 abs"></div>
<div class="card-img img-1 abs" role="img" aria-label="Photo of a woman stretching in a field under a pink sunset"></div>
<div class="card-img img-2 abs" role="img" aria-label="Photo of a doctor with a tablet talking to an older patient"></div>
<div class="card-body cb-1 abs"><h4>NULLAM DAPIBUS</h4><p>Praesent quis dapibus orci, a interdum ligula. Sed rutrum dignissim hendrerit laoreet molestie diam...</p><a href="#">READ MORE</a></div>
<div class="card-body cb-2 abs"><h4>NULLAM DAPIBUS</h4><p>Praesent quis dapibus orci, a interdum ligula. Sed rutrum dignissim hendrerit laoreet molestie diam...</p><a href="#">READ MORE</a></div>
<div class="dots proj-dots abs"><i class="on"></i><i></i><i></i></div>

<h2 class="section-title faq-title abs">FAQ’S</h2>
<div class="faq-item abs" style="top:3228px"><span>What makes this project unique?</span><b>+</b></div>
<div class="faq-item abs" style="top:3293px"><span>Does this project assume that the impact of religion is always positive?</span><b>+</b></div>
<div class="faq-item abs" style="top:3357px"><span>How can I collaborate?</span><b>+</b></div>
<div class="faq-item abs" style="top:3422px"><span>Will Harrowgate faculty lead all projects?</span><b>+</b></div>

<svg class="footer-bg abs" width="1200" height="340" viewBox="0 0 1200 340"><path d="M0 70 C300 0 900 0 1200 70 L1200 340 L0 340Z" fill="var(--grey)"/></svg>
<div class="brand footer-brand abs">
  <div class="brand-dot"></div>
  <div class="brand-name">Wellness, Meaning, and the Inner Journey<span>The Research Program</span></div>
</div>
<div class="f-col col-map abs"><h5>SITE MAP</h5><a href="#">Home</a><a href="#">People</a><a href="#">Projects</a><a href="#">FAQS</a><a href="#">Resources</a><a href="#">Contact Us</a></div>
<div class="f-col col-res abs"><h5>RESOURCES</h5><a href="#">Nemo enim ipsam</a><a href="#">Voluptatem quia</a><a href="#">Voluptas sit aspernatur</a><a href="#">Aut odit aut</a></div>
<div class="f-col col-mail abs"><h5>EMAIL SUBSCRIBE</h5></div>
<div class="subscribe abs"><span>Enter Email Address</span><b>GO</b></div>
<div class="social abs"><i></i><i></i><i></i><i></i><i></i></div>
<div class="copyright abs">Copyright © 2021. Company Name . All Right Reserved</div>

</body>
</html>
```